Weightloss company needs Business Card

We want a business card that is clean and professional, yet portrays that we are a friendly, innovative, and versatile program designed to fit the needs of our clients.
I would like there to be 2 sides, one side having an appointment card, and the other side containing the logo and business information. There can be decorations on both sides. The logo is attached.

Target Market(s)

Men and women 40-60

Industry/Entity Type

Business

Contact Information for Business Card

Font styles to use
Sans Serif

Requirements
Must have
• The logo, space for business information
Nice to have
• The colors in the logo
Should not have
• No pictures of people or food

```html
<!DOCTYPE html>
<html lang="en">
<head>
<meta charset="UTF-8">
<title>Renew Turn Wellness – Business Card</title>
<link href="https://fonts.googleapis.com/css2?family=Open+Sans:wght@400;600;700;800&display=swap" rel="stylesheet">
<style>
  :root{
    --bg:#ece8e2;
    --kraft:#c8a77e;
    --paper:#ffffff;
    --ink:#1b1a18;
    --ink-soft:#2e2b27;
    --shadow:rgba(60,40,20,.22);
  }
  *{box-sizing:border-box;margin:0;padding:0}
  html,body{width:1200px;height:900px;overflow:hidden}
  body{
    background:var(--bg);
    font-family:"Open Sans",Arial,sans-serif;
    color:var(--ink);
    position:relative;
  }
  .card{
    position:absolute;
    left:280px;
    width:640px;
    height:366px;
    background:var(--kraft);
    box-shadow:0 6px 18px var(--shadow);
    overflow:hidden;
  }
  .card--appointment{top:50px}
  .card--contact{top:484px}

  /* brand name */
  .brand{
    position:absolute;
    display:flex;
    align-items:center;
    gap:10px;
  }
  .brand__dot{
    width:12px;height:12px;border-radius:50%;
    background:var(--ink);
    flex:none;
  }
  .brand__name{
    font-weight:800;
    font-size:24px;
    letter-spacing:-.3px;
    line-height:1.2;
    color:var(--ink);
    white-space:nowrap;
  }

  /* appointment side */
  .appointment__band{
    position:absolute;
    left:0;right:0;top:66px;height:228px;
    background:var(--paper);
  }
  .card--appointment .brand{left:40px;top:80px}
  .appointment__form{
    position:absolute;
    left:190px;right:60px;top:130px;
    display:flex;flex-direction:column;gap:16px;
  }
  .appointment__title{
    font-weight:600;font-size:17px;letter-spacing:.3px;line-height:1.3;
    display:flex;align-items:flex-end;gap:6px;
    margin-left:30px;
  }
  .field{
    display:flex;align-items:flex-end;gap:6px;
    font-weight:700;font-size:15px;line-height:1.3;
  }
  .field__line{
    flex:1;
    border-bottom:2px dotted var(--ink-soft);
    height:1px;margin-bottom:4px;
  }
  .field__unit{font-weight:700;font-size:14px}
  .field--name{margin-left:60px}
  .field--date{margin-left:70px}
  .field--time{margin-left:80px}
  .appointment__notice{
    position:absolute;left:0;right:0;bottom:26px;
    text-align:center;
    font-weight:700;font-size:16px;letter-spacing:.2px;
  }

  /* contact side */
  .card--contact .brand{left:40px;top:160px}
  .contact{
    position:absolute;left:400px;top:104px;
    color:var(--ink-soft);
  }
  .contact__name{font-weight:600;font-size:19px;color:var(--ink)}
  .contact__role{font-size:13px;margin-bottom:18px}
  .contact__address{font-size:13px;line-height:1.45;margin-bottom:14px}
  .contact__list{list-style:none;font-size:13px;line-height:1.6}
  .contact__list li{display:flex;align-items:center;gap:10px}
  .contact__list svg{width:12px;height:12px;flex:none;fill:var(--ink)}
</style>
</head>
<body>

<section class="card card--appointment" aria-label="Appointment card">
  <div class="appointment__band"></div>
  <div class="brand">
    <span class="brand__dot"></span>
    <span class="brand__name">Renew Turn Wellness</span>
  </div>
  <div class="appointment__form">
    <div class="appointment__title">YOUR NEXT APPOINTMENT IS <span class="field__line"></span></div>
    <div class="field field--name">Name: <span class="field__line"></span></div>
    <div class="field field--date">Date: <span class="field__line"></span></div>
    <div class="field field--time">Time: <span class="field__line"></span><span class="field__unit">AM</span><span class="field__line"></span><span class="field__unit">PM</span></div>
  </div>
  <p class="appointment__notice">If unable to keep appointment, kindly give 24hrs notice.</p>
</section>

<section class="card card--contact" aria-label="Contact card">
  <div class="brand">
    <span class="brand__dot"></span>
    <span class="brand__name">Renew Turn Wellness</span>
  </div>
  <div class="contact">
    <p class="contact__name">Daniel Hart</p>
    <p class="contact__role">Managing Director</p>
    <p class="contact__address">12345, Address Goes Here<br>Country Name, 123456.</p>
    <ul class="contact__list">
      <li>
        <svg viewBox="0 0 24 24" aria-hidden="true"><path d="M6.6 10.8a15 15 0 0 0 6.6 6.6l2.2-2.2a1 1 0 0 1 1-.25 11.4 11.4 0 0 0 3.6.57 1 1 0 0 1 1 1V20a1 1 0 0 1-1 1A17 17 0 0 1 3 4a1 1 0 0 1 1-1h3.5a1 1 0 0 1 1 1c0 1.25.2 2.45.57 3.6a1 1 0 0 1-.25 1z"/></svg>
        055-210 987 654
      </li>
      <li>
        <svg viewBox="0 0 24 24" aria-hidden="true"><path d="M2 5h20v14H2z M3.5 6.5 12 13l8.5-6.5" fill="none" stroke="#1b1a18" stroke-width="2"/><path d="M2 5h20v2l-10 7L2 7z"/></svg>
        hello@renewturn.com
      </li>
      <li>
        <svg viewBox="0 0 24 24" aria-hidden="true"><path d="M10 14a4 4 0 0 0 5.7 0l4-4a4 4 0 0 0-5.7-5.7l-1.5 1.5M14 10a4 4 0 0 0-5.7 0l-4 4a4 4 0 0 0 5.7 5.7l1.5-1.5" fill="none" stroke="#1b1a18" stroke-width="2.4" stroke-linecap="round"/></svg>
        www.renewturn.com
      </li>
    </ul>
  </div>
</section>

</body>
</html>
```